Chimney Service company needs new business card design

We need a updated business card with our new logo added. We provide a full range of chimney services throughout Vermont and New Hampshire. The business card will be one sided and color. Attached is our current business card another document showing all the information we would like on the card.
We dont like a lot of flashy colors.... here is a link to our website to get an idea of our branding www.flueguardianvt.example

Target Market(s)

homeowners

Industry/Entity Type

Business

Contact Information for Business Card

See attached sheet for content.

Font styles to use
Serif
Sans Serif

Requirements
Must have
• all information provided on separate sheet
Should not have
• Additional information that may clogg up design

```html
<!DOCTYPE html>
<html lang="en">
<head>
<meta charset="utf-8">
<title>Flue Guardian – Business Card</title>
<link rel="stylesheet" href="https://fonts.googleapis.com/css2?family=Open+Sans:wght@400;600;700&display=swap">
<style>
  :root {
    --brand-red: #8c0c0f;
    --brand-red-line: #a3161b;
    --charcoal: #2b2b2b;
    --ink: #333333;
    --card-white: #f4f4f4;
    --card-shade: #e6e6e6;
    --backdrop: #c9c9c9;
    --icon-fill: #e9d3d3;
  }
  * { margin: 0; padding: 0; box-sizing: border-box; }
  html, body { width: 1200px; height: 576px; overflow: hidden; }
  body {
    background: var(--backdrop);
    position: relative;
    font-family: "Open Sans", Arial, sans-serif;
    color: var(--ink);
  }
  .card {
    position: absolute;
    top: 138px;
    width: 484px;
    height: 294px;
    border-radius: 13px;
    overflow: hidden;
    background: linear-gradient(180deg, var(--card-white), var(--card-shade));
  }
  .card--services { left: 82px; }
  .card--contact { left: 602px; width: 481px; height: 292px; }

  .brand-name {
    font-family: "Open Sans", Arial, sans-serif;
    font-weight: 600;
    line-height: 1;
    letter-spacing: 1px;
    text-transform: uppercase;
  }

  /* Services side */
  .services-header { position: absolute; inset: 0 0 auto 0; height: 160px; }
  .services-title {
    position: absolute; top: 44px; left: 0; right: 0;
    text-align: center; color: #ffffff; font-size: 27px;
  }
  .service-list {
    position: absolute; top: 166px; left: 0; right: 0;
    display: flex; justify-content: space-around; padding: 0 10px;
    list-style: none;
  }
  .service {
    display: flex; flex-direction: column; align-items: center;
    font-size: 11.5px; line-height: 1.25; text-align: center; color: #333;
    padding: 0 6px;
  }
  .service + .service { border-left: 1px solid #d2a9aa; }
  .service-icon {
    width: 44px; height: 42px; background: var(--icon-fill);
    border-radius: 3px; margin-bottom: 12px;
  }
  .site-line {
    position: absolute; top: 266px; left: 0; right: 0;
    display: flex; align-items: center; justify-content: center; gap: 10px;
    font-size: 12px; color: var(--ink);
  }
  .site-line::before, .site-line::after {
    content: ""; width: 94px; height: 2px; background: var(--brand-red-line);
  }
  .accent { color: var(--brand-red); }

  /* Contact side */
  .contact-title {
    position: absolute; top: 40px; left: 23px;
    color: var(--charcoal); font-size: 32px;
  }
  .service-area {
    position: absolute; top: 138px; left: 22px;
    color: var(--brand-red); font-weight: 700; font-size: 15px;
  }
  .since {
    position: absolute; top: 160px; left: 22px; width: 222px;
    display: flex; align-items: center; gap: 6px;
    font-size: 9.5px; color: #444;
  }
  .since::before, .since::after { content: ""; flex: 1; height: 2px; background: var(--brand-red-line); }
  .contact-list {
    position: absolute; top: 186px; left: 24px; list-style: none;
    font-size: 12px; line-height: 19px;
  }
  .contact-list li { display: flex; align-items: center; gap: 10px; }
  .contact-list svg { width: 11px; height: 11px; fill: var(--brand-red); }
  .strip {
    position: absolute; bottom: 0; color: #fff; font-size: 11.5px;
    display: flex; align-items: center;
  }
  .strip--insured {
    left: 0; width: 264px; height: 26px; padding-left: 22px;
    background: var(--brand-red); border-radius: 0 4px 0 0;
  }
  .strip--family {
    right: 0; width: 211px; height: 38px; justify-content: center;
    background: var(--charcoal); border-radius: 5px 0 0 0; color: #e6e6e6;
  }
</style>
</head>
<body>

<section class="card card--services" aria-label="Card front: services">
  <svg class="services-header" viewBox="0 0 484 160" preserveAspectRatio="none" aria-hidden="true">
    <path d="M0 0 H484 V112 C420 120 380 150 300 144 C200 138 90 110 0 100 Z" fill="var(--brand-red)"/>
    <path d="M484 112 C420 120 380 150 300 144 C360 154 430 140 484 128 Z" fill="var(--charcoal)"/>
  </svg>
  <div class="services-title brand-name">Flue Guardian</div>

  <ul class="service-list">
    <li class="service"><div class="service-icon" role="img" aria-label="Icon: brick chimney"></div>Full Masonry<br>Services</li>
    <li class="service"><div class="service-icon" role="img" aria-label="Icon: brick wall with handshake"></div>Historic Chimney<br>Restoration</li>
    <li class="service"><div class="service-icon" role="img" aria-label="Icon: steel liner in chimney"></div>Stainless<br>Steel Liners</li>
    <li class="service"><div class="service-icon" role="img" aria-label="Icon: bricks and trowel"></div>New Chimney<br>Installations</li>
    <li class="service"><div class="service-icon" role="img" aria-label="Icon: sweep brush in chimney"></div>Guild Certified<br>Chimney sweeps</li>
  </ul>

  <div class="site-line"><span>www.<span class="accent">flueguardianvt</span>.example</span></div>
</section>

<section class="card card--contact" aria-label="Card back: contact">
  <div class="contact-title brand-name">Flue Guardian</div>

  <div class="service-area">Serving VT and New Hampshire</div>
  <div class="since">SINCE 1989</div>

  <ul class="contact-list">
    <li>
      <svg viewBox="0 0 12 12" aria-hidden="true"><path d="M1 3.5C1 2 2.5 1 6 1s5 1 5 2.5V5H8.5V3.8H3.5V5H1Z M3 6h6l1.5 5h-9Z"/></svg>
      <span>802-555-0147</span>
    </li>
    <li>
      <svg viewBox="0 0 12 12" aria-hidden="true"><path d="M0 2h12v8H0Z M1 3l5 4 5-4" stroke="#fff" stroke-width="1"/></svg>
      <span>info@flueguardianvt.example</span>
    </li>
    <li>
      <svg viewBox="0 0 12 12" aria-hidden="true"><circle cx="6" cy="6" r="5.5"/><path d="M0.5 6h11M6 0.5v11M6 .5c-3 3-3 8 0 11M6 .5c3 3 3 8 0 11" stroke="#fff" stroke-width=".8" fill="none"/></svg>
      <span>www.<span class="accent">flueguardianvt</span>.example</span>
    </li>
  </ul>

  <div class="strip strip--insured">Fully Insured – Free Estimates</div>
  <div class="strip strip--family">Family Owned &amp; Operated</div>
</section>

</body>
</html>
```